Business Card Design

I need a logo and a business card design that can be used for my business stationary, Facebook page and in the future a website. I don't know if I need a large design for brochures and stationery and a small portion of that as the logo or business card design. I probably need some advice about that. My new company is called Willowbank Family Circle. I don't have all of my business contact details available yet, but I want to get the design ready, so that when all this information is available I can get the printing done quickly.I'm a social worker and my business will be providing parenting groups and counselling sessions for parents.I would like the logo and business card to be very feminine and pretty. I want a silhouette image of a Mother and Baby and decorative swirls of flowers/vines/leaves and butterflies.I have found some designs elsewhere that are along the lines of what I am looking for. These images are attached below, but the quality of these attachments is very poor as I photographed them with my phone.My preferred colours would be to use black and white, purple and/or pink, aqua and or blue/green.There are four logo/business card options attached. Logo option 1 - I really like the flower and vine design. Logo option 2 - again I like the flowers and leaf design and the use of colour and the silhouette image of the Mum and Baby; Logo option 3 - I like the butterflies and decorative swirls in this option and Logo option 4 - I think this design is the best for a logo. I love the mother and baby image. I don't like the tree branch and the birds but I like the way the hair has been incorporated into the branch. I prefer the design of the flowers/vine/leaves in the other options.

Industry/Entity Type

Business

Contact Information for Business Card

Company Name:Embrace Attachment ParentingMobile:0417 751 394Email:Currently sourcing - TBAContact Name:Janelle ApplegarthQualifications:Currently sourcing details - TBA

Font styles to use
Script

Colors
33a6d7
85cae6
886aae
6c459b
e667a6
eea4c8

Requirements
Must have
• My project must have an image of a mother and child, slightly encircled by the mother's hair perhaps in a heart shape, and the mother's hair becoming a beautiful filigree design of vine/leaves/flowers and with some butterfly somewhere.
• Can all of the Words be in the same font Attachment Parenting can be slightly smaller.
Nice to have
• I would like to also have a similar vine/leaves/flowers and maybe a butterfly on the opposite side of the card. Maybe the Mother/child image on the top left of the card and the other pattern on the bottom right.
• If possible the use of aqua, purple and pink.

```html
<!DOCTYPE html>
<html lang="en">
<head>
<meta charset="utf-8">
<title>Willowbank Family Circle – Business Card</title>
<link rel="stylesheet" href="https://fonts.googleapis.com/css2?family=Open+Sans:wght@400;600&display=swap">
<style>
  :root {
    --teal-deep: #12707f;
    --teal-bright: #139aa3;
    --mist: #d3e6e9;
    --mist-soft: rgba(211, 230, 233, 0);
    --ink: #3b3b3b;
    --charcoal: #3a3a3a;
    --paper: #ffffff;
  }
  * { margin: 0; padding: 0; box-sizing: border-box; }
  html, body { width: 1200px; height: 685px; overflow: hidden; background: var(--paper); }
  .card {
    position: relative;
    width: 1200px;
    height: 685px;
    background: var(--paper);
    font-family: "Open Sans", Arial, sans-serif;
    overflow: hidden;
  }
  .backdrop-wash {
    position: absolute;
    left: 700px;
    top: 30px;
    width: 490px;
    height: 580px;
    background:
      radial-gradient(ellipse 48% 50% at 40% 42%, var(--mist) 0%, rgba(211,230,233,0.75) 45%, var(--mist-soft) 100%),
      radial-gradient(ellipse 32% 28% at 68% 48%, rgba(214,236,238,0.9) 0%, var(--mist-soft) 100%);
  }
  .brand {
    position: absolute;
    left: 40px;
    top: 150px;
    width: 420px;
    display: flex;
    align-items: center;
    gap: 22px;
  }
  .brand-dot {
    flex: none;
    width: 34px;
    height: 34px;
    border-radius: 50%;
    background: var(--teal-bright);
  }
  .brand-name {
    color: var(--teal-bright);
    font-weight: 600;
    line-height: 1.1;
  }
  .brand-name .primary { display: block; font-size: 62px; letter-spacing: -0.5px; }
  .brand-name .secondary { display: block; font-size: 40px; margin-top: 6px; }
  .divider {
    position: absolute;
    left: 0;
    top: 414px;
    width: 679px;
    height: 12px;
    background: var(--teal-deep);
  }
  .contact { list-style: none; }
  .contact li {
    position: absolute;
    left: 34px;
    display: flex;
    align-items: center;
    white-space: nowrap;
  }
  .contact .email { top: 462px; }
  .contact .phone { top: 540px; }
  .contact svg { width: 48px; height: 44px; flex: none; }
  .contact span {
    margin-left: 52px;
    font-size: 29px;
    color: var(--ink);
  }
  .person {
    position: absolute;
    left: 700px;
    top: 344px;
    width: 480px;
    text-align: center;
  }
  .person-name {
    font-size: 49px;
    font-weight: 400;
    color: var(--ink);
    line-height: 1.1;
    white-space: nowrap;
  }
  .person-role {
    margin-top: 10px;
    font-size: 23px;
    color: var(--teal-deep);
    letter-spacing: 0.5px;
  }
  .footer-bands {
    position: absolute;
    left: 0;
    bottom: 0;
    width: 1200px;
    height: 46px;
  }
</style>
</head>
<body>
  <main class="card">
    <div class="backdrop-wash" role="img" aria-label="Soft faint decorative wash in pale aqua"></div>

    <header class="brand">
      <span class="brand-dot"></span>
      <div class="brand-name">
        <span class="primary">Willowbank</span>
        <span class="secondary">Family Circle</span>
      </div>
    </header>

    <div class="divider"></div>

    <ul class="contact">
      <li class="email">
        <svg viewBox="0 0 48 34" aria-hidden="true">
          <rect x="1" y="1" width="46" height="32" fill="var(--teal-bright)"/>
          <polyline points="1,1 24,20 47,1" fill="none" stroke="#fff" stroke-width="2.5"/>
          <line x1="1" y1="33" x2="18" y2="15" stroke="#fff" stroke-width="2"/>
          <line x1="47" y1="33" x2="30" y2="15" stroke="#fff" stroke-width="2"/>
        </svg>
        <span>Currently Sourcing</span>
      </li>
      <li class="phone">
        <svg viewBox="0 0 48 48" aria-hidden="true">
          <path d="M10 3 L18 3 L21 13 L15 18 C18 26 23 31 30 34 L35 28 L45 31 L45 39 C45 43 42 46 38 45 C20 42 6 28 3 10 C2 6 5 3 10 3 Z" fill="var(--teal-bright)"/>
        </svg>
        <span>0438 260 517</span>
      </li>
    </ul>

    <section class="person">
      <h1 class="person-name">Rosalind Thackeray</h1>
      <p class="person-role">(DIRECTOR)</p>
    </section>

    <svg class="footer-bands" viewBox="0 0 1200 46" aria-hidden="true">
      <polygon points="0,0 893,0 867,46 0,46" fill="var(--teal-deep)"/>
      <polygon points="913,0 1200,0 1200,46 887,46" fill="var(--charcoal)"/>
    </svg>
  </main>
</body>
</html>
```